Internet of Things Word Template

We need a new MS word template for our high-tech, Internet of Things business that matches the enclosed template in terms of content (chapters and subsections), but that updates the style to match our new house style, that has a clear and simple style sheet, uses NUMBERED sections (style = 1.2.3.4.5), a clear TOC and that more closely matches our new website and some of the new documents enclosed. Website (www.varnoti-iot.com) and house style guide www.varnoti-iot.com/private/style-guide. We prefer a lighter style, needs to be professional and credible. Current template has become difficult to work with, so prefer someone starting from scratch. Cover design should be more Internet of Things related than just security-oriented, and can draw from graphics on our website.

Target Market(s)

Technical decision makers at companies that make Internet of Things devices or chip manufacturers who make the chips that go into many devices across industries like medical, automotive, smart buildings, smart cities, car dealerships, trucking, etc.

Font styles to use
Sans Serif

Colors
1763aa
ec1f27
f78f20

Requirements
Must have
• Close relationship to house style from website... but...
Lightly implemented. Not too heavy. Doesn't look too dark when printed in black and white.
Must be easy for the average person to customize for their needs. My colleagues are not Word experts.
Nice to have
• A nicely designed cover. That's the one place to really express our brand.
Should not have
• No over-use of icons or illustrations in the document itself.

```html
<!DOCTYPE html>
<html lang="en">
<head>
<meta charset="utf-8">
<title>Varnoti – Word Template Pages</title>
<link rel="stylesheet" href="https://fonts.googleapis.com/css2?family=Work+Sans:wght@400;500;600;700;800&display=swap">
<style>
  :root {
    --blue: #1763aa;
    --orange: #f78f20;
    --ink: #444a52;
    --grey-text: #5f6368;
    --logo: #4d5560;
    --page-bg: #f2f2f2;
    --sheet: #ffffff;
    --faint: #eef1f5;
  }
  * { margin: 0; padding: 0; box-sizing: border-box; }
  html, body { width: 1200px; height: 3793px; overflow: hidden; }
  body {
    background: var(--page-bg);
    font-family: "Work Sans", Arial, sans-serif;
    color: var(--ink);
    position: relative;
  }
  .sheet {
    position: absolute;
    left: 96px;
    width: 1008px;
    height: 505px;
    background: var(--sheet);
    box-shadow: 0 2px 8px rgba(0,0,0,.12);
    overflow: hidden;
  }
  .sheet > * { position: absolute; }
  .brand {
    left: 93px; top: 30px;
    display: flex;
    align-items: center;
    gap: 10px;
    font-weight: 700;
    font-size: 28px;
    line-height: 1;
    color: var(--logo);
  }
  .brand-mark { width: 18px; height: 18px; background: var(--logo); }
  .accent-bar { background: var(--blue); width: 8px; }
  .title {
    color: var(--blue);
    font-weight: 700;
    font-size: 42px;
    line-height: 1;
    letter-spacing: .3px;
    white-space: nowrap;
  }
  .title-sm { font-size: 28px; }
  .body-copy {
    font-size: 11.5px;
    line-height: 20px;
    color: var(--grey-text);
  }
  .ghost-word {
    font-size: 120px;
    font-weight: 400;
    color: var(--faint);
    line-height: 1;
  }

  .eyebrow { color: var(--orange); font-weight: 700; font-size: 13px; letter-spacing: .3px; }
  .cover-sub { color: var(--blue); font-weight: 700; font-size: 14px; }
  .cover-date { color: var(--ink); font-weight: 700; font-size: 14px; letter-spacing: .5px; }

  .band { left: 0; width: 1008px; background: var(--blue); }
  .card { background: var(--sheet); box-shadow: 0 2px 10px rgba(0,0,0,.14); }
  .prop-col { width: 330px; text-align: center; font-size: 13.5px; font-weight: 500; color: #2e3338; }
  .prop-col li { list-style: none; height: 36px; line-height: 36px; }
  .rule-blue { background: var(--blue); height: 2px; }
  .rule-orange { background: var(--orange); width: 6px; }

  .toc { width: 340px; font-size: 15.5px; color: var(--grey-text); letter-spacing: .3px; }
  .toc li { list-style: none; height: 29px; line-height: 29px; display: flex; justify-content: space-between; }
  .toc .num { font-size: 13px; color: var(--grey-text); }
  .toc .lvl2 { padding-left: 22px; color: var(--blue); font-size: 14px; }
  .toc .lvl3 { padding-left: 48px; color: var(--blue); font-size: 14px; }

  .entry { font-size: 10.5px; color: var(--grey-text); display: flex; justify-content: space-between; width: 415px; }
  .frame { border: 6px solid; }
</style>
</head>
<body>

<section class="sheet" style="top:103px">
  <div class="brand"><span class="brand-mark"></span><span>VARNOTI</span></div>
  <div class="accent-bar" style="left:93px;top:213px;height:213px"></div>
  <p class="eyebrow" style="left:125px;top:210px">VARNOTI IOT SECURITY</p>
  <h1 class="title" style="left:125px;top:238px">LOREM IPSUM DOLOR</h1>
  <p class="body-copy" style="left:128px;top:290px;width:470px">Lorem ipsum dolor sit amet, consectetur adipiscing elit, sed do eiusmod tempor incididunt ut labore et dolore magna aliqua. Ut enim ad minim veniam, quis nostrud exercitationA</p>
  <p class="cover-sub" style="left:128px;top:366px">Lorem ipsum dolor</p>
  <p class="cover-date" style="left:128px;top:402px">05-06-2021</p>
  <div role="img" aria-label="Engineer in hard hat and safety vest using a transparent data screen in a factory" style="left:615px;top:0;width:299px;height:243px;background:linear-gradient(135deg,#1d2d44,#8a6a3a 55%,#2a3f5c)"></div>
  <div role="img" aria-label="Worker with laptop running face recognition on screen" style="left:615px;top:262px;width:299px;height:243px;background:linear-gradient(135deg,#3a3530,#8c7d6b 50%,#2b2f35)"></div>
</section>

<section class="sheet" style="top:720px">
  <div class="brand"><span class="brand-mark"></span><span>VARNOTI</span></div>
  <div role="img" aria-label="Engineer in white hard hat looking at a holographic machine control interface" style="left:306px;top:0;width:608px;height:266px;background:linear-gradient(120deg,#16263c,#2c5a8a 45%,#4fa3cf 65%,#12243a)"></div>
  <span class="ghost-word" style="left:690px;top:320px">IoT</span>
  <div class="accent-bar" style="left:93px;top:311px;height:159px"></div>
  <h2 class="title" style="left:125px;top:307px">COPYRIGHT NOTICE</h2>
  <p class="body-copy" style="left:128px;top:360px;width:460px">Varnoti IoT Security, a business unit of Halvern SA is a member of the Varnoti Group of Companies. This document is the intellectual property of Varnoti IoT Security and contains confidential and privileged information.&nbsp; The reproduction, modification, or communication to third parties (or to other than the addressee) of any part of this document is strictly prohibited without the prior written consent from Halvern SA.</p>
</section>

<section class="sheet" style="top:1335px">
  <div class="brand"><span class="brand-mark"></span><span>VARNOTI</span></div>
  <h2 class="title" style="right:93px;top:27px">DOCUMENT PROPERTIES</h2>
  <div class="band" style="top:110px;height:84px"></div>
  <div class="card" style="left:160px;top:110px;width:687px;height:371px"></div>
  <div class="rule-blue" style="left:276px;top:130px;width:227px"></div>
  <div class="rule-orange" style="left:496px;top:141px;height:303px"></div>
  <div class="rule-blue" style="left:505px;top:455px;width:225px"></div>
  <ul class="prop-col" style="left:169px;top:150px">
    <li>Version</li><li>File name</li><li>Publication date</li><li>Confidentiality Status</li>
    <li>Document owner</li><li>Document recipient</li><li>Document status</li><li>Client company name</li>
  </ul>
  <ul class="prop-col" style="left:480px;top:150px">
    <li>XX.YY</li><li>DOCUMENT1</li><li>DD.MM.YYYY</li><li>Confidentiality level</li>
    <li>Doc Owner Name</li><li>Recipient's name</li><li>Draft/Proposal/Reviewed/Approved</li><li>Client Company Name</li>
  </ul>
</section>

<section class="sheet" style="top:1952px">
  <div class="brand"><span class="brand-mark"></span><span>VARNOTI</span></div>
  <h2 class="title" style="right:93px;top:27px">TABLE OF CONTENTS</h2>
  <span class="ghost-word" style="left:690px;top:300px">IoT</span>
  <ul class="toc" style="left:93px;top:118px">
    <li><span>Document Properties</span><span class="num">3</span></li>
    <li><span>Table of Figures</span><span class="num">5</span></li>
    <li><span>Table of tables</span><span class="num">5</span></li>
    <li><span>Executive Summary</span><span class="num">6</span></li>
    <li><span>Introduction</span><span class="num">7</span></li>
    <li class="lvl2"><span>Subsection</span><span class="num">7</span></li>
    <li class="lvl3"><span>Subsection</span><span class="num">7</span></li>
    <li class="lvl3"><span>Subsection</span><span class="num">7</span></li>
    <li><span>Section Tile</span><span class="num">8</span></li>
    <li class="lvl2"><span>Subsection</span><span class="num">8</span></li>
    <li class="lvl3"><span>Subsection</span><span class="num">8</span></li>
  </ul>
  <div class="accent-bar" style="left:497px;top:118px;width:13px;height:324px"></div>
  <ul class="toc" style="left:583px;top:118px">
    <li><span>CODE HIGHLIGHTING</span><span class="num">9</span></li>
    <li class="lvl2"><span>CODE EXAMPLE</span><span class="num">9</span></li>
    <li><span>Document History</span><span class="num">10</span></li>
    <li><span>Document Recipients</span><span class="num">10</span></li>
    <li><span>Varnoti IoT Security Contact</span><span class="num">10</span></li>
    <li><span>References</span><span class="num">11</span></li>
    <li><span>Acronyms</span><span class="num">12</span></li>
    <li><span>Annexes</span><span class="num">13</span></li>
  </ul>
</section>

<section class="sheet" style="top:2569px">
  <div class="brand"><span class="brand-mark"></span><span>VARNOTI</span></div>
  <div class="accent-bar" style="left:93px;top:197px;width:6px;height:160px"></div>
  <h2 class="title title-sm" style="left:115px;top:194px">TABLE OF FIGURES</h2>
  <p class="entry" style="left:115px;top:237px"><span>Figure 1 Varnoti Security Site</span><span>7</span></p>
  <h2 class="title title-sm" style="left:115px;top:288px">TABLE OF TABLES</h2>
  <p class="entry" style="left:115px;top:332px"><span>Table 1 Table example</span><span>4</span></p>
  <div class="frame" role="img" aria-label="Hand touching a glowing network of connected points" style="left:567px;top:68px;width:184px;height:184px;border-color:var(--blue);background:linear-gradient(135deg,#e6eaf0,#5a6f8c 55%,#1a2a44)"></div>
  <div class="frame" role="img" aria-label="Tablet with network lines on a dark background" style="left:777px;top:82px;width:133px;height:131px;border-color:#5b6a7d;background:linear-gradient(135deg,#1c2a40,#38557a)"></div>
  <div class="frame" role="img" aria-label="Finger tapping a screen with light connections" style="left:582px;top:281px;width:134px;height:134px;border-color:#9a7550;background:linear-gradient(135deg,#3a4a60,#c78b7a 55%,#1f2c40)"></div>
  <div class="frame" role="img" aria-label="Connected device network over a city at dusk" style="left:737px;top:241px;width:184px;height:182px;border-color:var(--orange);background:linear-gradient(135deg,#2c4a70,#6c86a6 50%,#1a2a44)"></div>
</section>

<section class="sheet" style="top:3184px">
  <div class="brand"><span class="brand-mark"></span><span>VARNOTI</span></div>
  <div style="left:914px;top:49px;width:94px;height:409px;background:var(--orange)"></div>
  <div style="left:497px;top:49px;width:6px;height:409px;background:var(--orange)"></div>
  <div role="img" aria-label="Earth from space covered by a glowing network of connection lines" style="left:503px;top:0;width:411px;height:505px;background:radial-gradient(ellipse at 70% 45%,#9fd0f0 0%,#2f6fa8 25%,#0f2f55 60%,#071a33 100%)"></div>
  <div class="accent-bar" style="left:93px;top:197px;width:7px;height:174px"></div>
  <h2 class="title title-sm" style="left:115px;top:195px">EXECUTIVE SUMMARY</h2>
  <p class="body-copy" style="left:115px;top:235px;width:380px">Lorem ipsum dolor sit amet, consectetur adipisicing elit, sed do eiusmod tempor incididunt ut labore et dolore magna aliqua. Ut enim ad minim veniam, quis nostrud exercitation ullamco laboris nisi ut aliquip ex ea commodo consequat. Duis aute irure dolor in reprehenderit in voluptate velit esse cillum dolore eu fugiat nulla pariatur. Excepteur sint occaecat cupidatat non proident, sunt in culpa qui officia deserunt mollit anim id est laborum</p>
</section>

</body>
</html>
```